IV Nutritional Clinic Web Design

We are working with Velqo. They are an IV Nutritional Clinic and in need of a new website design.
Some sites to use for inspiration:
https://brightpathcareco.com
https://www.ourzavrowellness.com
https://www.dewspringlounge.com
https://qvitalsurge.com
https://www.lumo-vital.com/pages/iv-therapy-west-hollywood
https://www.tqoncologyhub.com/cancer-care/iv-drips/
https://dripwellary.com
https://corvinahealthhub.com
Thank you for taking the time to consider designing a website for us. We are web developers based in Stockton, CA, USA. Most of our projects go through the same process. Understanding this process may help you win a project with us. We custom-code all of our websites in-house. We don’t have any requirements as to what tools you use for your design, but we prefer Figma files. For any design that we label as four-stars, we send it to the client for review. The client picks the final design they want us to use. Once we complete this process, we will continue to show additional clients all the four-star sites and purchase them later. Your designs will have multiple chances to sell. For better chances of success, we ask that you follow these guidelines.
IMAGES:
If you use any images or icons in the design, we ask that you have a link to the asset so we can purchase the image/icon. Most of the designs we submit do not have the customer’s images on them unless they have some great images. Be creative; show us the feeling you are trying to portray with your image choices. Use any royalty-free site you choose. We subscribe to Pixvane and mainly use their images, but we can purchase images outside of Pixvane.
PLEASE NOTE: we will not submit designs to clients with watermarks on the images.
FONTS:
We ask that you identify the fonts used in the design. This can be done in a message if you want. We typically use Google Fonts and Pixvane Fonts.
CONTENT:
We're always open to different content and ideas. We often submit designs with stock images so the client can see our vision. We typically take pictures after the website launch to use their images with our vision. Lorem Ipsum is fine for paragraphs, but we ask that you write the headers in correct English. We want to be able to show the vision and identify the sections of the website.
INSPIRATION:
We typically add a couple of links in the brief of websites we like to help you get started in your design.
REVISIONS:
We do not often ask for revisions of the designs unless we see something in the design that may not appeal to the client. If there are slight changes that we want to make, we do that in the development process.
FEEDBACK:
We rarely give feedback on designs during the design process. We are working on many website projects and do not have the time to provide feedback. We usually respond if your request is well thought out and asks specific questions, but a note asking “feedback, please” usually goes unanswered.

```html
<!DOCTYPE html>
<html lang="en">
<head>
<meta charset="utf-8">
<title>Velqo Hydration — Expert IV Infusion</title>
<link href="https://fonts.googleapis.com/css2?family=Inter:wght@400;500;600;700;800&family=Noto+Sans:wght@400;500;600;700&family=Tinos:wght@700&display=swap" rel="stylesheet">
<style>
:root{
  --navy:#1b2453;
  --navy-deep:#1f2535;
  --green:#7aa445;
  --green-dark:#6a9238;
  --orange:#e3761c;
  --text:#6b6f7a;
  --light:#eef0f7;
  --white:#fff;
}
*{margin:0;padding:0;box-sizing:border-box}
html,body{width:1200px;height:4246px;overflow:hidden}
body{position:relative;font-family:"Inter",sans-serif;color:var(--text);background:var(--white)}
.abs{position:absolute}
.heading{font-family:"Noto Sans",sans-serif;color:var(--navy);font-weight:600}
.label{font-size:13px;color:var(--green);text-transform:uppercase;font-weight:500;letter-spacing:.3px}
.label-center{position:absolute;left:0;width:1200px;text-align:center}
.label-center span{border-bottom:1px solid var(--green);padding-bottom:2px}

/* updates bar */
.updates{top:0;left:0;width:1200px;height:30px;background:#f4f4f4;font-size:12px;display:flex;align-items:center;justify-content:center;gap:6px;color:#555}
.updates b{color:var(--orange);font-weight:700}
.updates i{display:inline-block;width:14px;height:10px;border:1.5px solid var(--orange);border-radius:2px;margin-right:6px}

/* header */
.header{top:30px;left:0;width:1200px;height:82px;background:var(--white)}
.logo{left:58px;top:12px;font-size:36px;font-weight:800;color:var(--navy);letter-spacing:1px;display:flex;align-items:center;gap:8px}
.logo-sub{left:60px;top:58px;width:120px;height:10px;background:var(--green)}
.nav{left:242px;top:0;height:82px;display:flex;align-items:center;gap:34px;font-size:11px;font-weight:700;color:var(--navy)}
.nav .active{color:var(--green)}
.enquiry{left:959px;top:14px;display:flex;gap:14px;align-items:center}
.enquiry .circle{width:48px;height:48px;border-radius:50%;background:#3a3d45;display:flex;align-items:center;justify-content:center}
.enquiry small{display:block;font-size:11px;color:var(--orange);font-weight:700}
.enquiry strong{font-size:15px;color:var(--navy)}

/* hero */
.hero{top:112px;left:0;width:1200px;height:700px;background:linear-gradient(100deg,#1d2a55 0%,#33466e 45%,#7d98ac 75%,#b9c7cf 100%)}
.hero-title-box{left:89px;top:152px;width:567px;height:77px;background:rgba(255,255,255,.18)}
.hero-title{left:89px;top:154px;font-family:"Tinos",serif;font-size:56px;color:var(--white)}
.hero-sub{left:89px;top:244px;width:580px;font-size:19px;font-weight:700;color:var(--white);line-height:29px}
.btn-green{background:var(--green);color:var(--white);font-weight:700;display:flex;align-items:center;justify-content:center}
.hero-btn{left:89px;top:331px;width:264px;height:45px;border-radius:23px;font-size:12px}

/* about */
.about-label{left:630px;top:766px}
.about-title{left:630px;top:796px;font-size:42px;line-height:53px;width:540px}
.about-sub{left:630px;top:930px;font-size:21px;font-family:"Noto Sans",sans-serif;color:var(--navy)}
.about-text{left:630px;top:978px;width:505px;font-size:13px;line-height:21.5px}
.about-btn{left:630px;top:1139px;width:155px;height:46px;font-size:15px;gap:14px;border-radius:2px}

/* services */
.services{top:1302px;left:0;width:1200px;height:565px;background:linear-gradient(100deg,#dfe3e9,#f0f1f4 50%,#d7dde4)}
.services-title{top:1436px;font-size:40px}
.card{background:var(--white);text-align:center;display:flex;flex-direction:column;align-items:center}
.card h3{font-family:"Noto Sans",sans-serif;font-weight:500;font-size:18px;color:var(--navy);margin-top:16px}
.card .bar{width:30px;height:3px;background:var(--green);margin:10px 0 14px}
.card p{font-size:11px;line-height:20px;width:230px;color:#888}
.card .more{font-size:11px;font-weight:700;color:#555;margin-top:14px}
.card.dark{background:#283266}
.card.dark h3,.card.dark p,.card.dark .more{color:var(--white)}
.card.dark .more{border:2px solid var(--white);padding:9px 30px}

/* testimonials */
.test-title{top:1972px;font-size:40px}
.avatar{border-radius:50%;border:3px solid var(--white);box-shadow:0 3px 10px rgba(0,0,0,.15)}
.quote-text{top:2284px;left:290px;width:620px;text-align:center;font-size:17px;line-height:31px;color:#7d818a}
.stars{top:2394px;left:0;width:1200px;text-align:center;color:var(--orange);font-size:20px;letter-spacing:2px}
.client-name{top:2424px;left:0;width:1200px;text-align:center;font-size:18px;font-weight:600;color:#555}
.client-role{top:2454px;left:0;width:1200px;text-align:center;font-size:10px;color:#888}
.arrow{width:44px;height:44px;border-radius:50%;display:flex;align-items:center;justify-content:center}

/* team */
.team{top:2546px;left:0;width:1200px;height:585px;background:linear-gradient(180deg,#e4e6ea,#f1f2f4)}
.team-title{top:2640px;font-size:40px}
.member{width:219px;height:304px;background:var(--white);box-shadow:0 4px 14px rgba(0,0,0,.06)}
.member .photo{width:219px;height:217px}
.member small{position:absolute;left:22px;top:233px;font-size:10px;color:var(--orange)}
.member strong{position:absolute;left:22px;top:254px;font-size:15px;color:#333}
.member .plus{position:absolute;right:22px;top:200px;width:28px;height:28px;background:var(--white);display:flex;align-items:center;justify-content:center;font-size:14px;color:#555}
.member.active{background:#3a3d45}
.member.active strong,.member.active small{color:var(--white)}
.member.active .plus{background:var(--green);color:var(--white)}
.socials{position:absolute;right:22px;top:8px;display:flex;flex-direction:column;gap:12px}
.socials span{width:28px;height:28px;background:var(--white);display:block}
.socials span:first-child{background:var(--green)}

/* contact */
.git{left:132px;top:3310px;font-size:34px;color:var(--navy);font-weight:400}
.git b{font-weight:700}
.git-text{left:134px;top:3357px;width:400px;font-size:12.5px;line-height:23px}
.info-icon{width:44px;height:44px;border-radius:50%;background:var(--green);display:flex;align-items:center;justify-content:center}
.info h4{font-size:13px;color:var(--navy);font-weight:700}
.info p{font-size:13px;line-height:22px;color:#555}
.social-circle{width:40px;height:40px;border-radius:50%;background:var(--navy)}
.form-box{left:593px;top:3283px;width:482px;height:389px;border:3px solid #e2e4ea;border-radius:6px;background:var(--white)}
.form-box h3{position:absolute;left:38px;top:32px;font-size:20px;color:var(--navy);font-weight:700}
.field{position:absolute;left:35px;width:415px;background:var(--light);font-size:12px;color:#555;padding:14px 24px}
.send{left:35px;top:301px;width:415px;height:48px;font-size:16px}

/* footer */
.footer{top:3734px;left:0;width:1200px;height:465px;background:var(--navy-deep)}
.f-panel{left:100px;top:72px;width:316px;height:328px;background:#262c3d;border-top:4px solid var(--green)}
.f-panel h3,.f-col h3{font-size:19px;font-weight:700;color:var(--white)}
.f-input{position:absolute;left:26px;width:263px;height:47px;background:#2e3446;border:1px solid #3c4356;color:var(--white);font-size:12px;font-weight:500;padding:15px 14px}
.f-submit{position:absolute;left:26px;top:251px;width:263px;height:50px;font-size:11px}
.f-list{list-style:none;font-size:14px;line-height:31px;color:#e7e8ec}
.f-list li::before{content:"- "}
.f-note{font-size:13.5px;line-height:21px;color:#e7e8ec}
.f-email{width:312px;height:42px;background:#2e3446;border-radius:4px;font-size:13px;color:var(--white);padding:12px 16px;position:relative}
.f-email .go{position:absolute;right:0;top:0;width:74px;height:42px;border-radius:6px;background:var(--green);display:flex;align-items:center;justify-content:center}
.f-soc{width:34px;height:34px;border-radius:50%;background:#343a4c}
.copy{top:4199px;left:0;width:1200px;height:47px;background:var(--green);color:var(--white);font-size:14px;font-weight:500;display:flex;align-items:center;justify-content:space-between;padding:0 104px 0 116px}
</style>
</head>
<body>

<div class="abs updates"><i></i><b>UPDATES:</b> Lorem ipsum dolor sit amet, consectetur adipiscing elit, sed do eiusmod tempor incididunt ut labore et dolore magna aliqua.</div>

<header class="abs header">
  <div class="abs logo">VELQO</div>
  <div class="abs logo-sub"></div>
  <nav class="abs nav">
    <span class="active">HOME</span><span>ABOUT US</span><span>TREATMENTS</span><span>NEW PATIENTS</span><span>FEES</span><span>CONTACT US</span>
  </nav>
  <div class="abs enquiry">
    <div class="circle"><svg width="22" height="22" viewBox="0 0 24 24"><path fill="#fff" d="M6.6 10.8a15 15 0 006.6 6.6l2.2-2.2a1 1 0 011-.25 11.4 11.4 0 003.6.57 1 1 0 011 1V20a1 1 0 01-1 1A17 17 0 013 4a1 1 0 011-1h3.5a1 1 0 011 1c0 1.25.2 2.45.57 3.57a1 1 0 01-.25 1z"/></svg></div>
    <div><small>ENQUIRIES</small><strong>+ 1-888-555-01-234</strong></div>
  </div>
</header>

<section class="abs hero" role="img" aria-label="Photo of a clinician in scrubs and mask treating a patient"></section>
<div class="abs hero-title-box"></div>
<h1 class="abs hero-title">Expert IV Infusion</h1>
<p class="abs hero-sub">Lorem ipsum dolor sit amet, consectetur adipiscing elit, se do eiusmod adipiscing elit</p>
<div class="abs btn-green hero-btn">SCHEDULE A FREE CONSULT</div>

<!-- curves framing about section -->
<svg class="abs" style="left:0;top:640px" width="1200" height="720" viewBox="0 0 1200 720">
  <path d="M0 170 C300 20 800 0 1200 40 L1200 0 L0 0 Z" fill="none"/>
  <path d="M0 170 Q400 10 1200 45 L1200 60 Q520 40 0 200 Z" fill="#ffffff"/>
  <path d="M0 165 Q380 20 880 17 Q420 40 0 185 Z" fill="var(--green)"/>
  <path d="M0 185 Q420 45 1200 58 L1200 560 L0 560 Z" fill="#fff"/>
  <path d="M1200 530 Q900 680 350 690 Q850 700 1200 560 Z" fill="var(--green)"/>
</svg>

<!-- about -->
<svg class="abs" style="left:90px;top:805px" width="500" height="410">
  <circle cx="240" cy="200" r="205" fill="#e3f0dc"/>
  <circle cx="58" cy="340" r="50" fill="var(--green)"/>
</svg>
<div class="abs" role="img" aria-label="Photo of a smiling doctor in a white coat with a stethoscope" style="left:135px;top:810px;width:390px;height:390px;border-radius:50%;background:radial-gradient(circle at 50% 40%,#c9b8a6,#8e9fa8 55%,#5f7381)"></div>
<div class="abs" role="img" aria-label="Photo of a doctor writing on a clipboard" style="left:376px;top:846px;width:188px;height:188px;border-radius:50%;border:4px solid #fff;background:linear-gradient(135deg,#c8d6e3,#7f9bb8)"></div>

<div class="abs label about-label"><span style="border-bottom:1px solid var(--green)">WHO WE ARE</span></div>
<h2 class="abs heading about-title">The team you can trust to get the job done</h2>
<div class="abs about-sub">Vital Nutrients, Amplified Wellness</div>
<p class="abs about-text">Lorem ipsum dolor sit amet, consectetur adipiscing elit, sed do eiusmod tempor incididunt ut labore et dolore magna aliqua. Ut enim ad minim veniam, quis nos trud exercitation ullamco laboris nisi ut aliquip ex ea commodo consequat.<br>Duis aute irure dolor in reprehenderit in voluptate velit esse cillum dolore eu fugiat nulla pariatur. Excepteur sint occaecat cupidatat non proident, sunt in culpa qui officia deserunt mollit anim id est laborum.</p>
<div class="abs btn-green about-btn">Contact us <svg width="18" height="14" viewBox="0 0 18 14"><path d="M1 7h15M10 1l6 6-6 6" stroke="#fff" stroke-width="2" fill="none"/></svg></div>

<!-- services -->
<section class="abs services" role="img" aria-label="Faint photo of a clinic treatment room"></section>
<svg class="abs" style="left:0;top:1180px" width="1200" height="150"><path d="M0 120 Q600 170 1200 0 L1200 0 L1200 0 Q850 150 350 150 Q150 150 0 122 Z" fill="#fff"/><path d="M1200 0 Q900 145 350 150 Q820 160 1200 25 Z" fill="var(--green)"/></svg>
<div class="label-center label" style="top:1401px"><span>OUR SERVICES</span></div>
<h2 class="abs heading label-center services-title">Services We Offer</h2>

<div class="abs" style="left:122px;top:1541px;width:82px;height:156px;background:var(--navy)"></div>
<div class="abs" style="left:997px;top:1660px;width:83px;height:153px;background:var(--navy)"></div>

<div class="abs card" style="left:133px;top:1552px;width:292px;height:251px;padding-top:24px">
  <svg width="44" height="44" viewBox="0 0 44 44"><path d="M22 6 L37 17 L31 36 L13 36 L7 17 Z" fill="none" stroke="var(--green)" stroke-width="3"/><circle cx="22" cy="6" r="3" fill="var(--green)"/><circle cx="37" cy="17" r="3" fill="var(--green)"/><circle cx="31" cy="36" r="3" fill="var(--green)"/><circle cx="13" cy="36" r="3" fill="var(--green)"/><circle cx="7" cy="17" r="3" fill="var(--green)"/></svg>
  <h3>Performance Boosters</h3><div class="bar"></div>
  <p>Lorem ipsum dolor sit amet, consectetur adipiscing elit, sed do adipiscing elit, sed do</p>
  <div class="more">LEARN MORE</div>
</div>
<div class="abs card dark" style="left:450px;top:1531px;width:301px;height:293px;padding-top:45px">
  <svg width="44" height="44" viewBox="0 0 44 44"><path d="M22 6 L37 17 L31 36 L13 36 L7 17 Z" fill="none" stroke="#fff" stroke-width="3"/><circle cx="22" cy="6" r="3" fill="#fff"/><circle cx="37" cy="17" r="3" fill="#fff"/><circle cx="31" cy="36" r="3" fill="#fff"/><circle cx="13" cy="36" r="3" fill="#fff"/><circle cx="7" cy="17" r="3" fill="#fff"/></svg>
  <h3>Hydration Therapy</h3><div class="bar" style="background:transparent;margin:2px 0 6px"></div>
  <p>Lorem ipsum dolor sit amet, consectetur adipiscing elit, sed do adipiscing elit, sed do</p>
  <div class="more">LEARN MORE</div>
</div>
<div class="abs card" style="left:778px;top:1552px;width:292px;height:251px;padding-top:24px">
  <svg width="44" height="44" viewBox="0 0 44 44"><path d="M22 6 L37 17 L31 36 L13 36 L7 17 Z" fill="none" stroke="var(--green)" stroke-width="3"/><circle cx="22" cy="6" r="3" fill="var(--green)"/><circle cx="37" cy="17" r="3" fill="var(--green)"/><circle cx="31" cy="36" r="3" fill="var(--green)"/><circle cx="13" cy="36" r="3" fill="var(--green)"/><circle cx="7" cy="17" r="3" fill="var(--green)"/></svg>
  <h3>Detox Infusions</h3><div class="bar"></div>
  <p>Lorem ipsum dolor sit amet, consectetur adipiscing elit, sed do adipiscing elit, sed do</p>
  <div class="more">LEARN MORE</div>
</div>

<!-- testimonials -->
<div class="label-center label" style="top:1938px"><span>TESTIMONIALS</span></div>
<h2 class="abs heading label-center test-title">Clients' Feedback</h2>
<svg class="abs" style="left:0;top:2100px" width="1200" height="200"><path d="M198 180 Q400 30 603 28 Q800 30 1009 180" fill="none" stroke="#3aa6b6" stroke-width="2" stroke-dasharray="9 7"/></svg>
<div class="abs avatar" role="img" aria-label="Client portrait" style="left:160px;top:2241px;width:76px;height:76px;background:#c9b3a2"></div>
<div class="abs avatar" role="img" aria-label="Client portrait" style="left:344px;top:2124px;width:76px;height:76px;background:#e6d8cf"></div>
<div class="abs avatar" role="img" aria-label="Client portrait" style="left:544px;top:2070px;width:118px;height:118px;background:#c6c8cc"></div>
<div class="abs avatar" role="img" aria-label="Client portrait" style="left:786px;top:2126px;width:76px;height:76px;background:#8c6a52"></div>
<div class="abs avatar" role="img" aria-label="Client portrait" style="left:971px;top:2241px;width:76px;height:76px;background:#b8a196"></div>
<svg class="abs" style="left:580px;top:2224px" width="42" height="34" viewBox="0 0 42 34"><path d="M2 34V18C2 8 7 2 16 0l2 5c-5 2-7 5-7 9h7v20zM24 34V18C24 8 29 2 38 0l2 5c-5 2-7 5-7 9h7v20z" fill="var(--navy)"/></svg>
<p class="abs quote-text">Lorem ipsum dolor sit amet, consectetur adipiscing elit, sed do eiusmod tem por incididunt ut labore et dolore magna aliqua. Ut enim ad minim veniam. labore et dolore magna aliq</p>
<div class="abs stars">★★★★★</div>
<div class="abs client-name">Mara Elston</div>
<div class="abs client-role">Client</div>
<div class="abs arrow" style="left:466px;top:2410px;background:var(--navy)"><svg width="12" height="14"><path d="M9 1L3 7l6 6" stroke="#fff" stroke-width="2" fill="none"/></svg></div>
<div class="abs arrow" style="left:696px;top:2410px;background:var(--green)"><svg width="12" height="14"><path d="M3 1l6 6-6 6" stroke="#fff" stroke-width="2" fill="none"/></svg></div>

<!-- team -->
<section class="abs team" role="img" aria-label="Faint photo of medical staff"></section>
<div class="label-center label" style="top:2606px"><span>OUR TEAM</span></div>
<h2 class="abs heading label-center team-title">Meet Our Team</h2>

<div class="abs member" style="left:122px;top:2746px">
  <div class="photo" role="img" aria-label="Photo of a nurse in green scrubs" style="background:linear-gradient(180deg,#dfe7ea,#8fb8ae)"></div>
  <div class="plus">+</div><small>Founder</small><strong>Ravel T. Okonne</strong>
</div>
<div class="abs member active" style="left:366px;top:2746px">
  <div class="photo" role="img" aria-label="Photo of a smiling older man with glasses" style="background:linear-gradient(180deg,#e4e4e4,#8b8f95)"></div>
  <div class="socials"><span></span><span></span><span></span><span></span></div>
  <div class="plus">+</div><small>Founder</small><strong>Ravel T. Okonne</strong>
</div>
<div class="abs member" style="left:595px;top:2746px">
  <div class="photo" role="img" aria-label="Photo of a doctor in a white coat" style="background:linear-gradient(180deg,#d8e2ea,#a9b7c4)"></div>
  <div class="plus">+</div><small>Founder</small><strong>Ravel T. Okonne</strong>
</div>
<div class="abs member" style="left:859px;top:2746px">
  <div class="photo" role="img" aria-label="Photo of a woman holding a tablet" style="background:linear-gradient(180deg,#eceae6,#b9a896)"></div>
  <div class="plus">+</div><small>Founder</small><strong>Ravel T. Okonne</strong>
</div>

<svg class="abs" style="left:0;top:3110px" width="1200" height="170"><path d="M0 160 Q300 10 1200 5 L1200 170 L0 170 Z" fill="#fff"/><path d="M0 160 Q250 20 850 8 Q330 30 0 140 Z" fill="var(--green)"/></svg>

<!-- contact -->
<h2 class="abs git">GET IN <b>TOUCH</b></h2>
<p class="abs git-text">Lorem ipsum dolor sit amet, consectetur adipiscing elit, sed do eiu smod tempor incididunt ut labore et dolore magna aliqua.</p>
<div class="abs info" style="left:128px;top:3432px;display:flex;gap:16px">
  <div class="info-icon"><svg width="18" height="22" viewBox="0 0 18 22"><path d="M9 0a8 8 0 00-8 8c0 6 8 14 8 14s8-8 8-14a8 8 0 00-8-8zm0 11a3 3 0 110-6 3 3 0 010 6z" fill="#fff"/></svg></div>
  <div style="padding-top:4px"><h4>LINDALE OFFICE</h4><p>24 Harbor Lane,<br>Suite 310, Lindale, Tv002</p></div>
</div>
<div class="abs info" style="left:128px;top:3532px;display:flex;gap:16px">
  <div class="info-icon"><svg width="20" height="20" viewBox="0 0 24 24"><path fill="#fff" d="M6.6 10.8a15 15 0 006.6 6.6l2.2-2.2a1 1 0 011-.25 11.4 11.4 0 003.6.57 1 1 0 011 1V20a1 1 0 01-1 1A17 17 0 013 4a1 1 0 011-1h3.5a1 1 0 011 1c0 1.25.2 2.45.57 3.57a1 1 0 01-.25 1z"/></svg></div>
  <div style="padding-top:6px"><h4>PHONE NUMBER</h4><p>+213 555- 0148</p></div>
</div>
<div class="abs" style="left:133px;top:3602px;display:flex;gap:8px"><span class="social-circle"></span><span class="social-circle"></span><span class="social-circle"></span></div>

<div class="abs form-box">
  <h3>LEAVE US A MESSAGE</h3>
  <div class="field" style="top:77px;height:43px">Email address</div>
  <div class="field" style="top:139px;height:43px">Subject</div>
  <div class="field" style="top:200px;height:96px">Write Your Message Here</div>
  <div class="abs btn-green send">SEND MESSAGE</div>
</div>

<!-- footer -->
<footer class="abs footer">
  <div class="abs f-panel">
    <h3 style="position:absolute;left:24px;top:28px">Contact Us</h3>
    <div class="f-input" style="top:78px">Enter Your Name</div>
    <div class="f-input" style="top:141px">Enter Your Mail</div>
    <div class="f-input" style="top:196px;height:47px">Enter Your Subject</div>
    <div class="btn-green f-submit">SUBMIT</div>
  </div>
  <div class="abs f-col" style="left:441px;top:106px">
    <h3>Informations</h3>
    <div style="display:flex;gap:40px;margin-top:14px">
      <ul class="f-list"><li>How it Works</li><li>Partners</li><li>Testimonials</li><li>Key Areas</li><li>Case Studies</li><li>Pricing</li></ul>
      <ul class="f-list"><li>Careers</li><li>Infrastructure</li><li>Client Support</li><li>Privacy Policy</li><li>Terms of Use</li><li>Sitemap</li></ul>
    </div>
  </div>
  <div class="abs f-col" style="left:783px;top:106px">
    <h3>Informations</h3>
    <p class="f-note" style="margin-top:16px">Subscribe to us &amp; receive our offers and updates<br>in your inbox directly</p>
    <div class="f-email" style="margin-top:18px">Your Email Address<span class="go"><svg width="18" height="14" viewBox="0 0 18 14"><path d="M1 7h15M10 1l6 6-6 6" stroke="#fff" stroke-width="2" fill="none"/></svg></span></div>
    <p class="f-note" style="margin-top:14px">* We do not share your email id</p>
    <div style="display:flex;gap:14px;margin-top:26px"><span class="f-soc"></span><span class="f-soc"></span><span class="f-soc"></span><span class="f-soc"></span></div>
  </div>
  <div class="abs" style="left:1116px;top:406px;width:40px;height:40px;border-radius:50%;border:2px solid var(--green);display:flex;align-items:center;justify-content:center"><svg width="14" height="10"><path d="M1 8l6-6 6 6" stroke="var(--green)" stroke-width="2" fill="none"/></svg></div>
</footer>
<div class="abs copy"><span>VELQO HYDRATION</span><span>Privacy Policy</span></div>

</body>
</html>
```